Selfpublisher sucht Buch-Cover für Roman (Thriller)
Zielgruppe
Ich bin Selfpublisher und möchte meinen dritten Roman veröffentlichen. Ich suche ein hochwertiges Cover, das im Buchhandel direkt ins Auge sticht.
Zielgruppe: junge Erwachsene/Erwachsene, Genre Thriller
Aufgabenstellung
Für meinen neuer Thriller „STILLE KAMMER“ suche ich ein aussagekräftiges Cover.
Es sollte den Inhalt des Buches widerspiegeln, den ich nachfolgend so gut es geht erläutere.
Klappentext:
Nie wieder Gewalt, Hass und Schmerz. Das schwor sich Larissa, als sie vor zwei Jahren aus ihrer lieblosen Ehe flüchtete und im Hamburger Frauenhaus ein sicheres Zuhause fand. Nun fühlt sie sich bereit, endlich wieder auf eigenen Füßen zu stehen. Doch während sie sich Stück für Stück zurück ins Leben kämpft, ahnt sie nichts von der Gefahr, die ganz in ihrer Nähe lauert.
Er beobachtet sie.
Er kennt jeden ihrer Schritte.
Er sammelt.
Und Stille Kammer wird mit Abstand sein größter Clou.
Ein Mörder. Ein Opfer. Ein Geheimnis, das beide für immer verbindet.
Weiterer Inhalt:
In der Geschichte kommt es zu blutigen Szenen, Kämpfen und Fluchtversuchen. Der Haupthandlungsort ist der Keller des Entführers. Das Cover sollte mehrere Inhalte dieses Kellers sowie das Opfer abbilden, dafür bin ich für Vorschläge offen. Um diesen Keller besser verstehen zu können, beschreibe ich ihn grob:
- Boden und Wände aus Beton, alt und schmutzig, Wasserflecken
- Das Entführungsopfer ist hinter deckenhohen Gitterstäben gefangen, die den Zellenraum mittig teilen
- Das Opfer ist innerhalb dieser Zelle zusätzlich mit einer Kette versehen, die mit einem Ring am Hals und einer Öse in der Wand befestigt ist
- Im Zellenraum gibt es ein altes Bett mit Metallgestell sowie eine Toilette. Ein kleines Kellerfenster (vergittert), das sich über einem Heizkörper befindet, stellt den einzigen Bezug zur Außenwelt dar
Das Opfer:
- Junge Frau, 29 Jahre alt
- äußerst schlank
- blond
- trägt beigefarbene Gefangenenkleidung (schlichte Stoffhose, schlichtes Oberteil mit Knöpfen und kurzen Ärmeln, einfache Socken)
- ist festgekettet (Halsring aus Eisen, daran eine Kette, die ins Mauerwerk führt)

```html
<!DOCTYPE html>
<html lang="de">
<head>
<meta charset="utf-8">
<title>Stille Kammer – Holger Brandt – Umschlag</title>
<link href="https://fonts.googleapis.com/css2?family=Lato:wght@400;700;900&family=Poppins:ital,wght@0,400;1,400&display=swap" rel="stylesheet">
<style>
  :root {
    --page-bg: #e6e8e9;
    --cover-dark: #151515;
    --cover-mid: #3a3a3a;
    --concrete: #4b4b4b;
    --blood: #b3121a;
    --blood-deep: #6e0b10;
    --ink-light: #f2f2f2;
    --ink-soft: #d9d9d9;
    --title-grey: #bdbdbd;
  }
  * { margin: 0; padding: 0; box-sizing: border-box; }
  html, body { width: 1200px; height: 1128px; overflow: hidden; background: var(--page-bg); }
  .cover-wrap {
    position: absolute; left: 60px; top: 174px;
    width: 1080px; height: 780px;
    display: flex;
    box-shadow: 0 20px 40px rgba(0,0,0,.25);
  }
  .panel { position: relative; height: 780px; overflow: hidden; background: var(--cover-dark); }
  .back-cover, .front-cover { width: 520px; }
  .spine { width: 40px; background: linear-gradient(90deg, #111, #262626 50%, #111); }

  .wall-texture {
    position: absolute; inset: 0;
    background:
      radial-gradient(ellipse at 30% 35%, rgba(120,120,120,.35), transparent 60%),
      radial-gradient(ellipse at 70% 70%, rgba(90,90,90,.3), transparent 55%),
      linear-gradient(180deg, var(--cover-mid), var(--cover-dark) 70%, #0d0d0d);
  }
  .front-cover .blood-splash {
    position: absolute; right: 0; top: 0; width: 360px; height: 260px;
    background: radial-gradient(ellipse at 80% 25%, rgba(179,18,26,.75), rgba(110,11,16,.35) 45%, transparent 70%);
  }
  .back-cover .blood-splash {
    position: absolute; left: 60px; right: 0; bottom: 0; height: 200px;
    background: radial-gradient(ellipse at 60% 70%, rgba(179,18,26,.85), rgba(110,11,16,.45) 50%, transparent 75%);
  }
  .cellar-window {
    position: absolute; left: 48px; top: 56px; width: 104px; height: 92px;
    background: radial-gradient(circle at 45% 45%, #f4f4f4, #a8a8a8 60%, #4a4a4a);
  }
  .back-cover .shadow-figure {
    position: absolute; left: 60px; top: 20px; width: 440px; height: 560px;
    background: radial-gradient(ellipse at 50% 45%, rgba(0,0,0,.55), transparent 70%);
  }

  .title-art { position: absolute; inset: 0; }
  .author {
    font-family: 'Lato', sans-serif; font-weight: 400; fill: var(--ink-light);
  }
  .title-big { font-family: 'Lato', sans-serif; font-weight: 900; }
  .title-sub { font-family: 'Lato', sans-serif; font-weight: 400; fill: var(--ink-light); }
  .genre { font-family: 'Lato', sans-serif; font-weight: 400; fill: var(--ink-light); }

  .blurb {
    position: absolute; left: 50px; top: 268px; width: 420px;
    font-family: 'Poppins', sans-serif; font-size: 12.5px; line-height: 19.5px;
    color: var(--ink-soft);
  }
  .blurb p { margin-bottom: 19px; }
  .blurb .lead { font-style: italic; text-align: center; display: block; }
  .blurb .closing { text-align: center; }
  .blurb em { font-style: italic; }

  .spine-text {
    position: absolute; left: 50%; top: 30px;
    transform: translateX(-50%);
    writing-mode: vertical-rl;
    font-family: 'Lato', sans-serif; color: var(--ink-soft);
    display: flex; gap: 60px; white-space: nowrap;
  }
  .spine-author { font-size: 13px; letter-spacing: 1px; }
  .spine-title { font-size: 19px; font-weight: 700; letter-spacing: 2px; }
</style>
</head>
<body>
<main class="cover-wrap">

  <section class="panel back-cover">
    <div class="wall-texture" role="img" aria-label="Verschmutzte Betonwand im Keller mit Wasserflecken und dunkler Silhouette"></div>
    <div class="shadow-figure"></div>
    <div class="blood-splash" role="img" aria-label="Rote Blutspritzer am unteren Rand"></div>
    <svg class="title-art" width="520" height="780" viewBox="0 0 520 780">
      <text class="title-big" x="185" y="137" font-size="92" fill="var(--title-grey)" textLength="150" lengthAdjust="spacingAndGlyphs">STIL</text>
      <text class="title-big" x="185" y="216" font-size="92" fill="var(--title-grey)" textLength="150" lengthAdjust="spacingAndGlyphs">LE</text>
      <text class="title-sub" x="185" y="241" font-size="26" textLength="150" lengthAdjust="spacingAndGlyphs">KAMMER</text>
    </svg>
    <div class="blurb">
      <p><span class="lead">Nie wieder Gewalt, Hass und Schmerz.</span>
      Das schwor sich Larissa, als sie vor zwei Jahren aus ihrer lieblosen Ehe flüchtete und im Hamburger Frauenhaus ein sicheres Zuhause fand. Nun fühlt sie sich bereit, endlich wieder auf eigenen Füßen zu stehen. Doch während sie sich Stück für Stück zurück ins Leben kämpft, ahnt sie nichts von der Gefahr, die ganz in ihrer Nähe lauert.</p>
      <p>Er beobachtet sie.<br>Er kennt jeden ihrer Schritte.<br>Er <em>sammelt</em>.<br>Und Stille Kammer wird mit Abstand sein größter Clou.</p>
      <p class="closing">Ein Mörder. Ein Opfer. Ein Geheimnis,<br>das beide für immer verbindet.</p>
    </div>
  </section>

  <section class="panel spine">
    <div class="spine-text">
      <span class="spine-author">HOLGER BRANDT</span>
      <span class="spine-title">STILLE KAMMER</span>
    </div>
  </section>

  <section class="panel front-cover">
    <div class="wall-texture" role="img" aria-label="Alte Kellerwand aus Beton mit Ketten über dem Titel"></div>
    <div class="blood-splash" role="img" aria-label="Rote Blutspritzer oben rechts"></div>
    <div class="cellar-window" role="img" aria-label="Vergittertes Kellerfenster mit einfallendem Licht"></div>
    <svg class="title-art" width="520" height="780" viewBox="0 0 520 780">
      <text class="author" x="452" y="181" font-size="30" text-anchor="end">HOLGER BRANDT</text>
      <text class="title-big" x="66" y="386" font-size="256" fill="var(--ink-light)" textLength="391" lengthAdjust="spacingAndGlyphs">STIL</text>
      <text class="title-big" x="66" y="593" font-size="272" fill="var(--ink-light)" textLength="391" lengthAdjust="spacingAndGlyphs">LE</text>
      <text class="title-sub" x="66" y="662" font-size="70" textLength="391" lengthAdjust="spacingAndGlyphs">KAMMER</text>
      <text class="genre" x="457" y="702" font-size="22" text-anchor="end">THRILLER</text>
    </svg>
  </section>

</main>
</body>
</html>
```